Wireless Internet Service Provider website design

We need a Internet Service Provider website that show the packages that we offer as well as the functionality where customers have the option of clicking on the various packages and be linked to a page where they can sign up for our services.
We need about 10-15 pages.
A. Integrated online store.
B. Live chat.
C. Social media page
My old website. Brightlinkradio.nyc

Example: http://plumcrestnet.com/services/residential/ Added Tuesday, June 7, 2016

Target Market(s)

Residential and small businesses

Industry/Entity Type

Internet

Coding

Coded - Design and coding required

Number of Pages Required

5+ page

Font styles to use
Serif
Sans Serif
Script

Colors
3176b5
85cae6
ffffff

Requirements
Must have
• Online store and live chat, drop down details on pricing from current website
Nice to have
• great design, functional website,

```html
<!DOCTYPE html>
<html lang="en">
<head>
<meta charset="utf-8">
<title>Brightlink Radio — Wireless Internet</title>
<link href="https://fonts.googleapis.com/css2?family=Arimo:wght@400;700&family=Open+Sans:ital,wght@0,400;0,600;1,400&display=swap" rel="stylesheet">
<style>
:root{
  --brand:#3176b5;
  --brand-dark:#0f5fa3;
  --teal:#1db3cf;
  --teal-soft:#85cae6;
  --ink:#222;
  --muted:#8a8a8a;
  --line:#e2e2e2;
  --grey-head:#a3a3a3;
  --navy:#0b2a4a;
  --navy-deep:#071c33;
  --white:#fff;
}
*{box-sizing:border-box;margin:0;padding:0}
html,body{width:1200px;height:2782px;overflow:hidden}
body{font-family:"Open Sans",sans-serif;color:var(--ink);background:var(--white);font-size:13px}
h1,h2,h3,h4{font-family:"Arimo",sans-serif;font-weight:400}
a{color:inherit;text-decoration:none}

/* header */
.site-header{height:100px;position:relative}
.brand{position:absolute;left:117px;top:30px;display:flex;align-items:center;gap:10px}
.brand-mark{width:30px;height:30px;background:var(--brand);border-radius:4px}
.brand-name{font-family:"Arimo",sans-serif;font-weight:700;font-size:30px;color:var(--brand);letter-spacing:-.5px}
.topbar{position:absolute;right:125px;top:16px;display:flex;gap:22px;font-size:13px;font-weight:600}
.topbar span{display:flex;align-items:center;gap:6px}
.main-nav{position:absolute;right:120px;top:55px;display:flex;gap:36px;font-family:"Arimo",sans-serif;font-size:14px;color:#555;text-transform:uppercase}
.main-nav .active{color:var(--brand)}

/* hero */
.hero{height:478px;position:relative;background:radial-gradient(ellipse at 62% 75%,#1f6fae 0%,#0b3b6a 35%,#041629 75%)}
.hero-copy{position:absolute;left:125px;top:158px}
.hero h1{color:var(--white);font-size:31px;line-height:46px;text-transform:uppercase;letter-spacing:.5px}
.btn-hero{display:inline-block;margin-top:26px;width:150px;height:46px;line-height:46px;text-align:center;background:var(--teal);color:var(--white);font-family:"Arimo",sans-serif;font-size:18px}
.slider-dots{position:absolute;left:565px;bottom:24px;display:flex;gap:6px}
.slider-dots i{width:16px;height:16px;border-radius:50%;background:var(--white)}
.slider-dots i:first-child{background:none;border:2px solid var(--white)}

/* welcome */
.welcome{height:330px;text-align:center;padding-top:36px}
.section-mark{width:40px;height:40px;border-radius:50%;background:var(--brand);margin:0 auto}
.welcome h2{font-size:23px;margin-top:24px;letter-spacing:.3px}
.welcome p{width:860px;margin:18px auto 0;color:var(--muted);font-size:12.5px;line-height:24px}
.btn-small{display:inline-block;padding:0 24px;height:32px;line-height:32px;background:var(--brand-dark);color:var(--white);font-size:11px;font-weight:600;margin-top:18px}

/* services */
.services{height:358px;background:var(--teal);display:flex;justify-content:center;gap:0;padding-top:58px}
.service{width:330px;text-align:center;color:var(--white)}
.service-icon{width:116px;height:116px;border:3px solid var(--white);border-radius:50%;margin:0 auto;display:flex;align-items:center;justify-content:center}
.service h3{font-size:19px;margin-top:22px}
.service p{font-size:12.5px;line-height:24px;margin-top:6px;color:#e6f7fb}
.btn-outline{display:inline-block;width:112px;height:34px;line-height:30px;border:2px solid var(--white);font-size:11px;font-weight:600;margin-top:12px}

/* pricing */
.pricing{height:476px;text-align:center;padding-top:22px}
.pricing h2{font-size:23px;margin-top:14px}
.price-table{display:flex;justify-content:center;align-items:flex-start;margin-top:18px}
.plan{width:221px;border:1px solid var(--line);border-right:none;background:var(--white);height:292px}
.plan:nth-child(3){border-right:1px solid var(--line)}
.plan-name{height:40px;line-height:40px;background:var(--grey-head);color:var(--white);font-family:"Arimo",sans-serif;font-size:18px}
.plan-price{font-family:"Arimo",sans-serif;color:var(--brand);font-size:46px;margin-top:10px}
.plan-price sup{font-size:20px;vertical-align:24px;margin-right:4px}
.plan-price small{font-size:24px}
.plan ul{list-style:none;width:180px;margin:10px auto 0;font-size:11.5px;color:#555}
.plan li{border-bottom:1px solid var(--line);line-height:23px}
.plan li:first-child{border:none;margin-bottom:6px}
.plan li:last-child{border:none}
.btn-plan{display:block;width:188px;height:38px;line-height:38px;margin:8px auto 0;background:var(--brand-dark);color:var(--white);font-family:"Arimo",sans-serif;font-size:15px}
.plan.featured{width:240px;height:328px;margin-top:-14px;border:1px solid #ccc;box-shadow:0 0 6px rgba(0,0,0,.15)}
.plan.featured .plan-name{background:var(--brand-dark);height:44px;line-height:44px;font-size:20px}
.plan.featured .plan-price{font-size:48px}
.plan.featured ul{font-size:12.5px}
.plan.featured li{line-height:26px}
.plan.featured .btn-plan{width:202px;height:42px;line-height:42px;font-size:17px}

/* testimonials */
.testimonials{height:343px;position:relative;background:linear-gradient(90deg,#4a3a33 0%,#7a6258 30%,#5c4a43 55%,#8c7466 80%,#4e3d37 100%);text-align:center;padding-top:40px}
.testimonials h2{color:var(--white);font-size:29px;position:relative}
.quote-row{display:flex;justify-content:center;gap:24px;margin-top:20px}
.quote{width:310px;height:158px;background:rgba(40,40,40,.85);border:2px solid #d8d8d8;text-align:left;padding:18px 26px;position:relative}
.quote p{color:var(--white);font-style:italic;font-size:11.5px;line-height:20px}
.quote cite{display:block;color:var(--teal);font-style:normal;font-size:12px;margin-top:10px}
.avatar{position:absolute;right:18px;bottom:-44px;width:78px;height:86px}

/* features */
.features{height:380px;position:relative}
.features h2{position:absolute;left:113px;top:18px;font-size:27px;line-height:40px;width:500px}
.features p{position:absolute;left:113px;top:124px;width:570px;font-size:11.5px;line-height:20px;color:var(--muted)}
.feature-links{position:absolute;left:107px;top:225px;display:flex;gap:48px}
.feature{display:flex;align-items:center;gap:14px;color:var(--teal);font-family:"Arimo",sans-serif;font-size:17px;line-height:22px}
.feature-icon{width:52px;height:52px;border-radius:50%;background:var(--teal);display:flex;align-items:center;justify-content:center}
.social-box{position:absolute;left:768px;top:3px;width:300px;height:340px;border:1px solid var(--line);box-shadow:0 1px 4px rgba(0,0,0,.1)}
.social-box h4{height:48px;line-height:48px;padding-left:24px;background:#f6f6f6;border-bottom:1px solid var(--line);color:var(--brand);font-size:16px}
.page-card{display:flex;gap:12px;margin:16px 0 0 22px}
.page-thumb{width:72px;height:60px;border:1px solid var(--line);display:flex;align-items:center;justify-content:center}
.page-thumb i{width:32px;height:32px;background:var(--brand);border-radius:4px}
.page-card b{display:block;color:var(--brand);font-weight:400;font-size:13px}
.like-btn{display:inline-block;background:var(--brand);color:var(--white);font-size:9px;padding:1px 6px;margin-top:4px}
.page-card small{display:block;font-size:10px;margin-top:4px}
.fan-grid{display:grid;grid-template-columns:repeat(5,46px);gap:10px;margin:18px 0 0 22px}
.fan-grid span{height:46px;background:linear-gradient(160deg,#b79a86,#6e5a50)}
.plugin-note{display:flex;align-items:center;gap:6px;margin:16px 0 0 22px;font-size:10px;color:#555}
.plugin-note i{width:13px;height:13px;background:var(--brand)}

/* footer */
.site-footer{height:257px;background:linear-gradient(180deg,var(--navy) 0%,#0a2440 100%);color:var(--white);position:relative}
.footer-col{position:absolute;top:45px}
.footer-col h4{font-size:16px;margin-bottom:14px}
.footer-col li{list-style:none;font-size:11.5px;line-height:22px;color:#dbe6f0}
.col-links{left:124px}.col-res{left:304px}.col-news{left:569px}.col-contact{left:848px}
.col-news p{font-size:11.5px;color:#dbe6f0}
.email-field{width:220px;height:28px;background:var(--white);margin-top:12px;color:#999;font-size:10px;line-height:28px;padding-left:12px;display:flex;align-items:center;gap:8px}
.btn-subscribe{display:inline-block;width:96px;height:30px;line-height:30px;text-align:center;background:var(--teal);font-size:12px;font-weight:600;margin-top:12px}
.btn-chat{display:flex;align-items:center;gap:8px;width:120px;height:34px;background:var(--teal);border:1px solid #7fd3e4;padding-left:12px;font-family:"Arimo",sans-serif;font-size:16px;margin-top:30px}
.col-contact address{font-style:normal;font-size:11.5px;line-height:22px;color:#dbe6f0}
.contact-line{display:flex;align-items:center;gap:8px;font-size:15px;margin-top:6px}
.contact-line.small{font-size:11.5px}
.social-row{display:flex;gap:8px;margin-top:14px}
.social-row i{width:30px;height:30px;border:2px solid var(--white);border-radius:50%}
.copyright{height:60px;background:var(--navy-deep);color:#9fb2c6;font-size:11px;text-align:center;line-height:60px}
</style>
</head>
<body>

<header class="site-header">
  <a class="brand" href="#"><span class="brand-mark"></span><span class="brand-name">Brightlink Radio</span></a>
  <div class="topbar">
    <span><svg width="14" height="14" viewBox="0 0 24 24"><path fill="#3176b5" d="M6.6 10.8a15 15 0 0 0 6.6 6.6l2.2-2.2c.3-.3.7-.4 1-.2 1.1.4 2.3.6 3.6.6.6 0 1 .4 1 1V20c0 .6-.4 1-1 1A17 17 0 0 1 3 4c0-.6.4-1 1-1h3.5c.6 0 1 .4 1 1 0 1.3.2 2.5.6 3.6.1.3 0 .7-.2 1z"/></svg>(866)-555-0142</span>
    <span><svg width="15" height="14" viewBox="0 0 24 22"><path fill="#3176b5" d="M0 1h4l3 12h13l3-9H6" stroke="#3176b5" stroke-width="0"/><path fill="none" stroke="#3176b5" stroke-width="2.4" d="M0 2h4l3 11h13l2.5-8H5.5"/><circle cx="9" cy="18" r="2" fill="#3176b5"/><circle cx="18" cy="18" r="2" fill="#3176b5"/></svg>Shopping Cart</span>
  </div>
  <nav class="main-nav">
    <a class="active" href="#">Home</a><a href="#">Why Brightlink</a><a href="#">Plan &amp; Packages</a><a href="#">Gallery</a><a href="#">Contact</a>
  </nav>
</header>

<section class="hero" role="img" aria-label="Glowing globe at night wrapped in a network of connected light points">
  <div class="hero-copy">
    <h1>Locally Own . Reliable .<br>Super Fast Internet</h1>
    <a class="btn-hero" href="#">BUY PLAN</a>
  </div>
  <div class="slider-dots"><i></i><i></i><i></i><i></i></div>
</section>

<section class="welcome">
  <div class="section-mark"></div>
  <h2>WELCOME TO BRIGHTLINK RADIO</h2>
  <p>Brightlink Radio is a highly reputable company, which is aiming at providing high quality internet access and phone services to a market that is continually growing. We are dedicated to filling the digital gap that has been created in the middle and lowe. When shopping for internet access, people usually look for what is reliable, fast and affordable. This description fits Brightlink Radio LCC the best. Customers who have subscribed to our services are enjoying some of the fastest speeds to be provided by</p>
  <a class="btn-small" href="#">READ MORE</a>
</section>

<section class="services">
  <div class="service">
    <div class="service-icon"><svg width="62" height="56" viewBox="0 0 62 56" fill="none" stroke="#fff" stroke-width="2.5"><rect x="4" y="4" width="22" height="16"/><rect x="36" y="4" width="22" height="16"/><path d="M15 20v10M47 20v10M4 40h54M31 30v10"/><circle cx="15" cy="40" r="3"/><circle cx="47" cy="40" r="3"/><path d="M15 30h32"/></svg></div>
    <h3>Residential Internet Access</h3>
    <p>Brightlink's VOIP home phone solutions<br>offer you a reliable, portable</p>
    <a class="btn-outline" href="#">READ MORE</a>
  </div>
  <div class="service">
    <div class="service-icon"><svg width="60" height="60" viewBox="0 0 60 60" fill="none" stroke="#fff" stroke-width="2.5"><rect x="10" y="6" width="26" height="46" rx="3"/><path d="M20 46h6"/><circle cx="38" cy="34" r="14"/><path d="M24 34h28M38 20v28M28 25c6 3 14 3 20 0M28 43c6-3 14-3 20 0"/></svg></div>
    <h3>Business Internet Access</h3>
    <p>Brightlink's VOIP home phone solutions<br>offer you a reliable, portable</p>
    <a class="btn-outline" href="#">READ MORE</a>
  </div>
  <div class="service">
    <div class="service-icon"><svg width="64" height="64" viewBox="0 0 64 64" fill="none" stroke="#fff" stroke-width="2.5"><circle cx="32" cy="32" r="26"/><path d="M10 22c14 2 30 10 40 26M22 8c-4 14 2 34 22 50M36 6c8 8 18 10 24 10" /></svg></div>
    <h3>Unlimited Internet Usage</h3>
    <p>Brightlink's VOIP home phone solutions<br>offer you a reliable, portable</p>
    <a class="btn-outline" href="#">READ MORE</a>
  </div>
</section>

<section class="pricing">
  <div class="section-mark"></div>
  <h2>OUR PRICING</h2>
  <div class="price-table">
    <div class="plan">
      <div class="plan-name">Brightlink Simplicity</div>
      <div class="plan-price"><sup>$</sup>39<small>.99</small></div>
      <ul><li>Includes:</li><li>Free smart router</li><li>Free internet protection</li><li>Unlimited Brightlink Wi-Fi<br>access</li></ul>
      <a class="btn-plan" href="#">TRY IT NOW</a>
    </div>
    <div class="plan">
      <div class="plan-name">Brightlink Value Pack</div>
      <div class="plan-price"><sup>$</sup>45<small>.95</small></div>
      <ul><li>Includes:</li><li>Free smart router</li><li>Free internet protection</li><li>Unlimited Brightlink Wi-Fi<br>access</li></ul>
      <a class="btn-plan" href="#">TRY IT NOW</a>
    </div>
    <div class="plan">
      <div class="plan-name">Brightlink Super Pack</div>
      <div class="plan-price"><sup>$</sup>69<small>.99</small></div>
      <ul><li>Includes:</li><li>Free smart router</li><li>Free internet protection</li><li>Unlimited Brightlink Wi-Fi<br>access</li></ul>
      <a class="btn-plan" href="#">TRY IT NOW</a>
    </div>
    <div class="plan featured">
      <div class="plan-name">Brightlink Speed</div>
      <div class="plan-price"><sup>$</sup>89<small>.99</small></div>
      <ul><li>Includes:</li><li>Free smart router</li><li>Free internet protection</li><li>Unlimited Brightlink Wi-Fi<br>access</li></ul>
      <a class="btn-plan" href="#">TRY IT NOW</a>
    </div>
  </div>
</section>

<section class="testimonials" role="img" aria-label="Blurred background photo of people at home enjoying their connection">
  <h2>Testimonials</h2>
  <div class="quote-row">
    <blockquote class="quote">
      <p>"Thanks for your great service. I love my internet and your quick response to my questions and concerns. I would definitely refer Brightlink to my friends and family. Keep up the good work."</p>
      <cite>Marcus Hale</cite>
      <svg class="avatar" viewBox="0 0 78 86" role="img" aria-label="Customer portrait"><polygon points="39,2 76,22 76,64 39,84 2,64 2,22" fill="#c9ad98" stroke="#fff" stroke-width="4"/></svg>
    </blockquote>
    <blockquote class="quote">
      <p>"By far the best customer service I have ever received from an Internet service provider. Brightlink stands above the rest, thanks for the rapid resolution to my problem."</p>
      <cite>Owen Ridley</cite>
      <svg class="avatar" viewBox="0 0 78 86" role="img" aria-label="Customer portrait"><polygon points="39,2 76,22 76,64 39,84 2,64 2,22" fill="#bfa590" stroke="#fff" stroke-width="4"/></svg>
    </blockquote>
    <blockquote class="quote">
      <p>"Brightlink is the best internet servicer provider in Brooklyn, finally a better option to internet service. My family and I are enjoying faster downloads streaming movies, thank you for your fast</p>
      <cite>Clara Benton</cite>
      <svg class="avatar" viewBox="0 0 78 86" role="img" aria-label="Customer portrait"><polygon points="39,2 76,22 76,64 39,84 2,64 2,22" fill="#d2b7a2" stroke="#fff" stroke-width="4"/></svg>
    </blockquote>
  </div>
</section>

<section class="features">
  <h2>Fast download &amp; upload speeds at an affordable price</h2>
  <p>When choosing among the best high speed internet providers, there are several other factors that should be taken into consideration besides just the available download speeds. Upload speeds are important as well, though they probably are not as crucial as download speeds.</p>
  <div class="feature-links">
    <a class="feature" href="#"><span class="feature-icon"><svg width="26" height="24" viewBox="0 0 26 24" fill="none" stroke="#fff" stroke-width="2.4"><path d="M3 4h20v12H11l-6 5v-5H3z"/></svg></span>Customer<br>Support center</a>
    <a class="feature" href="#"><span class="feature-icon"><svg width="26" height="26" viewBox="0 0 26 26"><circle cx="13" cy="13" r="8" fill="none" stroke="#fff" stroke-width="5" stroke-dasharray="4 2.3"/><circle cx="13" cy="13" r="3" fill="#fff"/></svg></span>Equipment<br>Options</a>
    <a class="feature" href="#"><span class="feature-icon"><svg width="26" height="26" viewBox="0 0 26 26"><path d="M13 2l3.3 7 7.5.8-5.6 5 1.6 7.4L13 18.4l-6.8 3.8 1.6-7.4-5.6-5 7.5-.8z" fill="none" stroke="#fff" stroke-width="2.2"/></svg></span>Customer<br>Guarantee</a>
  </div>
  <aside class="social-box">
    <h4>Follow us on Friendwall</h4>
    <div class="page-card">
      <div class="page-thumb"><i></i></div>
      <div><b>Brightlink Radio</b><span class="like-btn">Like</span><small>71 people like Brightlink Radio</small></div>
    </div>
    <div class="fan-grid" role="img" aria-label="Grid of follower profile photos">
      <span></span><span></span><span></span><span></span><span></span>
      <span></span><span></span><span></span><span></span><span></span>
    </div>
    <div class="plugin-note"><i></i>Friendwall social plugin</div>
  </aside>
</section>

<footer class="site-footer">
  <div class="footer-col col-links">
    <h4>Quick Links</h4>
    <ul><li>Refer a Friend</li><li>Free Internet for life</li><li>Terms &amp; Conditions</li><li>Privacy Policy</li><li>Site Map</li></ul>
  </div>
  <div class="footer-col col-res">
    <h4>Resources</h4>
    <ul><li>Wireless Internet Access Agreement</li><li>Brightlink Internet Access</li><li>Customer Support Center</li><li>Catalog</li></ul>
  </div>
  <div class="footer-col col-news">
    <h4>Newsletter Sign Up</h4>
    <p>Please Sign up here for latest deals</p>
    <div class="email-field"><svg width="12" height="9" viewBox="0 0 12 9"><rect width="12" height="9" fill="#999"/><path d="M0 0l6 5 6-5" stroke="#fff" fill="none"/></svg>Enter your email</div>
    <a class="btn-subscribe" href="#">Subscribe</a>
    <a class="btn-chat" href="#"><svg width="22" height="18" viewBox="0 0 22 18" fill="none" stroke="#fff" stroke-width="2"><path d="M2 2h12v8H7l-4 3v-3H2z"/><path d="M16 6h4v8h-1v3l-4-3H9v-2"/></svg>Live Chat</a>
  </div>
  <div class="footer-col col-contact">
    <h4>Contact Us</h4>
    <address>2480 Harbor Avenue<br>3rd Fl Brooklyn, NY 11230</address>
    <div class="contact-line"><svg width="16" height="16" viewBox="0 0 24 24"><path fill="none" stroke="#fff" stroke-width="2" d="M6.6 10.8a15 15 0 0 0 6.6 6.6l2.2-2.2c.3-.3.7-.4 1-.2 1.1.4 2.3.6 3.6.6.6 0 1 .4 1 1V20c0 .6-.4 1-1 1A17 17 0 0 1 3 4c0-.6.4-1 1-1h3.5c.6 0 1 .4 1 1 0 1.3.2 2.5.6 3.6.1.3 0 .7-.2 1z"/></svg>866-555-0142</div>
    <div class="contact-line small"><svg width="16" height="12" viewBox="0 0 16 12"><rect x="1" y="1" width="14" height="10" fill="none" stroke="#fff" stroke-width="1.5"/><path d="M1 1l7 6 7-6" fill="none" stroke="#fff" stroke-width="1.5"/></svg>support@brightlinkradio.nyc</div>
    <div class="social-row" aria-label="Social links"><i></i><i></i><i></i><i></i></div>
  </div>
</footer>
<div class="copyright">© 2016 Company Name &nbsp;All right reserved &nbsp;Term of Use</div>

</body>
</html>
```